Flyer Design Project

Training and Consulting Flyer
Updates

I attached a document that contained the wording for the flyer as well as the logo.

Target Market(s)

Maple Bridge agencies and grantees

Industry/Entity Type

Training

Font styles to use
Sans Serif

Colors
e667a6
eda3c7
a54499
b768aa
f9d9e8

Requirements
Must have
• Words provided on attachment
Nice to have
• Graphics that are related to adult training/learning and consulting

```html
<!DOCTYPE html>
<html lang="en">
<head>
<meta charset="utf-8">
<title>Wren Health Consultants – Flyer and Cover</title>
<link href="https://fonts.googleapis.com/css2?family=Roboto+Condensed:ital,wght@0,400;0,700;1,700&display=swap" rel="stylesheet">
<style>
:root{
  --magenta:#b51f6e;
  --magenta-soft:#e667a6;
  --pink-mid:#eda3c7;
  --pink-pale:#f9d9e8;
  --plum:#a54499;
  --ink:#151515;
  --paper:#ffffff;
  --backdrop:#e4e4e6;
}
*{box-sizing:border-box;margin:0;padding:0}
html,body{width:1200px;height:1200px;overflow:hidden;background:var(--backdrop)}
body{position:relative;font-family:"Roboto Condensed",Arial,sans-serif;color:var(--ink)}
.page{position:absolute;top:237px;width:566px;height:726px;background:var(--paper);overflow:hidden;box-shadow:0 2px 10px rgba(0,0,0,.18)}
.flyer{left:20px}
.cover{left:614px}

/* flyer header */
.header-strip{position:absolute;left:0;top:34px;width:34px;height:120px;background:var(--magenta)}
.brand{position:absolute;left:34px;top:34px;width:230px;height:120px;display:flex;flex-direction:column;align-items:center;justify-content:center;gap:8px}
.brand-name{display:flex;align-items:center;gap:10px;font-weight:700;font-size:23px;line-height:1.05;color:var(--ink);text-transform:uppercase;white-space:nowrap}
.brand-dot{flex:none;width:14px;height:14px;border-radius:50%;background:var(--magenta)}
.tagline{font-weight:400;font-size:13px;letter-spacing:.4px;text-transform:uppercase;white-space:nowrap}
.header-band{position:absolute;left:264px;top:34px;width:302px;height:120px;background:var(--magenta);color:#fff;padding:30px 0 0 16px}
.pillars{font-size:17.5px;word-spacing:2px}
.group{font-size:23.5px;margin-top:4px}

.headline{position:absolute;left:0;top:176px;width:566px;text-align:center;font-size:18px;line-height:23px}
.headline em{font-style:italic;font-weight:700;color:var(--magenta)}
.rule{position:absolute;height:4px;background:var(--magenta)}
.rule-top{left:0;top:240px;width:440px}
.rule-bottom{left:212px;top:383px;width:354px}
.photo{position:absolute;top:245px;height:138px}
.photo-stretch{left:0;width:173px;background:linear-gradient(135deg,#d9d6d3,#b6a9a2 60%,#8f8c8a)}
.photo-nutrition{left:173px;width:203px;background:radial-gradient(circle at 50% 75%,#e8a060,#f4efe9 60%,#ffffff)}
.photo-cyclist{left:376px;width:190px;background:linear-gradient(180deg,#6fa3d8,#a9c9e6 45%,#c9d64a 80%,#6e7a3a)}

.intro{position:absolute;left:40px;top:403px;width:500px;font-weight:700;font-size:13px;line-height:16.5px}
.services{position:absolute;left:36px;top:451px;width:510px;list-style:none}
.services li{position:relative;padding-left:30px;font-size:10.3px;line-height:13px;margin-bottom:13px;min-height:26px}
.services li::before{content:"";position:absolute;left:2px;top:4px;width:16px;height:16px;border-radius:50%;border:1.5px solid var(--magenta)}

.footer-line{position:absolute;left:0;top:616px;width:566px;height:3px;background:var(--ink)}
.footer{position:absolute;left:0;top:619px;width:566px;height:107px;background:var(--magenta);color:#fff}
.signatory{position:absolute;left:42px;top:26px;font-size:26px}
.signatory small{font-size:15px;margin-left:2px}
.footer-divider{position:absolute;left:231px;top:12px;width:1px;height:58px;background:rgba(255,255,255,.8)}
.contacts{position:absolute;left:248px;top:6px;list-style:none;font-size:12px}
.contacts li{display:flex;align-items:center;gap:12px;height:22px}
.contacts svg{width:12px;height:12px;fill:#fff}

/* cover */
.cover-brand{position:absolute;left:0;top:62px;width:566px;display:flex;flex-direction:column;align-items:center;gap:14px}
.cover-brand .brand-name{font-size:36px;gap:14px}
.cover-brand .brand-dot{width:20px;height:20px}
.cover-brand .tagline{font-size:19px}
.tree-art{position:absolute;left:60px;top:210px;width:446px;height:410px;background:radial-gradient(ellipse 48% 42% at 50% 45%,#e3a2d8,var(--pink-pale) 70%,rgba(255,255,255,0) 100%)}
.cover-pillars{position:absolute;left:0;top:352px;width:566px;text-align:center;font-size:24px;line-height:26px}
.cover-group{font-size:30px;line-height:32px}
.cover-footer{position:absolute;left:0;bottom:0;width:566px;height:130px}
.cover-footer svg{position:absolute;inset:0;width:100%;height:100%}
.cover-signatory{position:absolute;left:0;top:58px;width:566px;text-align:center;color:#fff;font-size:26px}
.cover-signatory small{font-size:15px}
</style>
</head>
<body>

<section class="page flyer">
  <div class="header-strip"></div>
  <div class="brand">
    <div class="brand-name"><span class="brand-dot"></span><span>Wren Health<br>Consultants</span></div>
    <div class="tagline">Care Through Knowledge</div>
  </div>
  <div class="header-band">
    <div class="pillars">Knowledge | Analysis | Statistics</div>
    <div class="group">Health Consultants &amp; Group</div>
  </div>

  <p class="headline">Innovative Approaches to meeting the 5 year funding measures<br>in the content area of <em>Health, Nutrition, Oral Health &amp; Safety</em></p>

  <div class="rule rule-top"></div>
  <div class="photo photo-stretch" role="img" aria-label="Photo of a woman stretching during a fitness session"></div>
  <div class="photo photo-nutrition" role="img" aria-label="Photo of a smiling woman choosing fresh fruit and vegetables over fast food"></div>
  <div class="photo photo-cyclist" role="img" aria-label="Photo of a cyclist in a helmet holding a bicycle under a blue sky"></div>
  <div class="rule rule-bottom"></div>

  <p class="intro">Wren Health consultants has embarked on a new methodology deigned ensure programs meet total requirements as prescribed under the health Services program.</p>
  <ul class="services">
    <li>Let us manage your health tips program through remote and offsite measures to ensure total compliance and strategic methodology toward quality service approaches.</li>
    <li>Let us provide consultants to mentor your health manager nutrition content specialist facilities safety manager these support consultant are advanced level academies in their specialized areas of focus.</li>
    <li>Let us provide advanced based Mock Reviews for your program designed to assist management staff in focus I, Focus II Review strategies for 2018.</li>
    <li>Let us provide T/ TA for any new Health, Nutrition and Safety staff to ensure they are fully prepared to perform their job duties at their highest level of management approaches.</li>
  </ul>

  <div class="footer-line"></div>
  <footer class="footer">
    <div class="signatory">Dana Morrow <small>CEO</small></div>
    <div class="footer-divider"></div>
    <ul class="contacts">
      <li><svg viewBox="0 0 24 24"><path d="M12 2a10 10 0 1 0 5 18.7l-1-1.7A8 8 0 1 1 20 12v1a2 2 0 0 1-4 0V7h-2v1a5 5 0 1 0 .8 7A4 4 0 0 0 22 13v-1A10 10 0 0 0 12 2zm0 13a3 3 0 1 1 0-6 3 3 0 0 1 0 6z"/></svg>info@wrenhealthconsult.com</li>
      <li><svg viewBox="0 0 24 24"><path d="M6.6 10.8a15 15 0 0 0 6.6 6.6l2.2-2.2a1 1 0 0 1 1-.25 11 11 0 0 0 3.6.6 1 1 0 0 1 1 1V20a1 1 0 0 1-1 1A17 17 0 0 1 3 4a1 1 0 0 1 1-1h3.5a1 1 0 0 1 1 1c0 1.25.2 2.45.6 3.6a1 1 0 0 1-.25 1z"/></svg>(555) 014-2290</li>
      <li><svg viewBox="0 0 24 24"><path d="M12 2a7 7 0 0 0-7 7c0 5.2 7 13 7 13s7-7.8 7-13a7 7 0 0 0-7-7zm0 9.5A2.5 2.5 0 1 1 12 6.5a2.5 2.5 0 0 1 0 5z"/></svg>P.O. Box 410 Fairhaven, GA 30000</li>
    </ul>
  </footer>
</section>

<section class="page cover">
  <div class="cover-brand">
    <div class="brand-name"><span class="brand-dot"></span><span>Wren Health<br>Consultants</span></div>
    <div class="tagline">Care Through Knowledge</div>
  </div>
  <div class="tree-art" role="img" aria-label="Illustration of a pink tree whose crown is made of fluttering butterflies"></div>
  <div class="cover-pillars">
    <div>Knowledge | Analysis | Statistics</div>
    <div class="cover-group">Health Consultants &amp; Group</div>
  </div>
  <div class="cover-footer">
    <svg viewBox="0 0 566 130" preserveAspectRatio="none"><path d="M0 22 Q283 -18 566 28 L566 130 L0 130 Z" fill="var(--magenta)"/></svg>
    <div class="cover-signatory">Dana Morrow <small>CEO</small></div>
  </div>
</section>

</body>
</html>
```